Veldmark Supplies Business Card

Professional business card that stand out to our potential customers. Front and back with clean modern design

Industry/Entity Type

Oil and gas

Contact Information for Business Card

Name, address, website , office phone and cell number

Requirements
Must have
• Editable files for each employee

```html
<!DOCTYPE html>
<html lang="en">
<head>
<meta charset="utf-8">
<title>Veldmark Supplies Business Card</title>
<link rel="stylesheet" href="https://fonts.googleapis.com/css2?family=Montserrat:wght@400;500;700&display=swap">
<style>
  :root {
    --stage: #ecebe8;
    --brand-blue: #00aed1;
    --brand-red: #e8202a;
    --paper: #ffffff;
    --ink: #1d1d1f;
    --shadow: rgba(0, 0, 0, 0.18);
  }
  * { margin: 0; padding: 0; box-sizing: border-box; }
  html, body {
    width: 1200px; height: 931px; overflow: hidden;
    background: var(--stage);
    font-family: "Montserrat", sans-serif;
    color: var(--ink);
  }
  .stage { position: relative; width: 1200px; height: 931px; }
  .card {
    position: absolute;
    width: 560px; height: 320px;
    border-radius: 18px;
    box-shadow: 0 10px 28px var(--shadow);
    overflow: hidden;
  }
  .card-front { left: 70px; top: 80px; background: var(--brand-blue); }
  .card-back { left: 570px; top: 520px; background: var(--paper); }

  .wordmark {
    display: flex; align-items: center; gap: 12px;
    font-weight: 700; text-transform: uppercase; letter-spacing: 0.04em;
  }
  .wordmark-square { display: block; flex: none; }
  .card-front .wordmark {
    position: absolute; left: 0; right: 0; top: 50%;
    transform: translateY(-50%);
    justify-content: center;
    color: var(--paper); font-size: 34px;
  }
  .card-front .wordmark-square { width: 34px; height: 34px; background: var(--brand-red); }

  .card-back .wordmark {
    position: absolute; right: 34px; top: 50px;
    color: var(--brand-red); font-size: 20px;
  }
  .card-back .wordmark-square { width: 22px; height: 22px; background: var(--brand-blue); }

  .rule {
    position: absolute; left: 34px; right: 34px; top: 108px;
    height: 1.5px; background: var(--brand-red);
  }
  .person { position: absolute; left: 34px; top: 132px; }
  .person-name { color: var(--brand-red); font-weight: 700; font-size: 26px; line-height: 1.1; }
  .person-title { font-size: 15px; margin-top: 4px; }

  .contacts {
    position: absolute; left: 34px; top: 200px;
    list-style: none; font-size: 13px; line-height: 1;
  }
  .contacts li { display: flex; align-items: center; gap: 10px; margin-bottom: 9px; }
  .contacts svg { width: 14px; height: 14px; flex: none; fill: var(--brand-blue); }

  .address {
    position: absolute; right: 34px; bottom: 34px;
    text-align: right; font-size: 12.5px; line-height: 1.4;
  }
</style>
</head>
<body>
<main class="stage">
  <section class="card card-front" aria-label="Card front">
    <div class="wordmark"><span class="wordmark-square"></span>Veldmark Supplies</div>
  </section>

  <section class="card card-back" aria-label="Card back">
    <div class="wordmark"><span class="wordmark-square"></span>Veldmark Supplies</div>
    <div class="rule"></div>
    <div class="person">
      <p class="person-name">Daniel Ostrow</p>
      <p class="person-title">President</p>
    </div>
    <ul class="contacts">
      <li>
        <svg viewBox="0 0 16 16" aria-hidden="true"><path d="M2 5c0-2 3-3 6-3s6 1 6 3v1h-3V5H5v1H2zM3 8h10l1 6H2zm5 1.5a2 2 0 1 0 0 4 2 2 0 0 0 0-4z"/></svg>
        +1.555.210.0400 x123
      </li>
      <li>
        <svg viewBox="0 0 16 16" aria-hidden="true"><path d="M3 1l3 3-2 2c1 2 4 5 6 6l2-2 3 3-2 2C7 15 1 9 1 3z"/></svg>
        +1.555.123.456
      </li>
      <li>
        <svg viewBox="0 0 16 16" aria-hidden="true"><path d="M1 3h14v1L8 9 1 4zm0 3l7 5 7-5v7H1z"/></svg>
        info@veldmarksupplies.com
      </li>
      <li>
        <svg viewBox="0 0 16 16" aria-hidden="true"><circle cx="8" cy="8" r="7"/></svg>
        www.veldmarksupplies.com
      </li>
    </ul>
    <p class="address">42 Ridgeline Avenue<br>Carver Falls, TX 79701 USA</p>
  </section>
</main>
</body>
</html>
```